Business Card Design for a new Senior Concierge Business 1.3.24

I need a professional business card to handout at networking events for my senior helper business. I would like to use the logo I have uploaded. The design should be clear and easy to read and should list the following information...
Delia Parkhurst
Owner
www.HarborlightElderAides.com
Brindle Falls, Texas
936.482.5079
Delia@harborlightelderaides.com

Target Market(s)

Senior Citizens

Industry/Entity Type

Personal Helper/ Assisstant

Contact Information for Business Card

I have included the details in the project description box.

Font styles to use
Serif

Colors
0054AA
0677BA
7BADD7
CADEEF
E8F1F8
59FF00
82FF00
B8FF75
E3FFCB
F4FFEA
E54698
E96AAD
F1A4CE
F9D9EA
FCEFF6
6B429C
8869AF
B7A5CE
E3DAEB
F3F0F8

Requirements
Must have
• Include uploaded logo
Nice to have
• The log that has been uploaded
Should not have
• No crazy fonts

```html
<!DOCTYPE html>
<html lang="en">
<head>
<meta charset="utf-8">
<title>Harborlight Elder Aides – Business Card</title>
<link rel="stylesheet" href="https://fonts.googleapis.com/css2?family=Lato:wght@400;700;900&display=swap">
<style>
  :root {
    --stage: #2a2a2a;
    --card: #ffffff;
    --purple: #6530e6;
    --pink: #dd1f5c;
    --teal: #0a8f94;
    --ink: #1c1c1c;
  }
  * { margin: 0; padding: 0; box-sizing: border-box; }
  html, body { width: 1047px; height: 1200px; overflow: hidden; }
  body {
    background: var(--stage);
    font-family: "Lato", sans-serif;
    position: relative;
  }
  .card {
    position: absolute;
    left: 156px;
    width: 743px;
    height: 425px;
    background: var(--card);
    border-radius: 20px;
    overflow: hidden;
  }
  .card--front { top: 120px; }
  .card--back { top: 634px; }

  .front-brand {
    position: absolute;
    left: 40px;
    top: 130px;
    width: 240px;
    text-align: center;
    color: var(--purple);
    font-weight: 700;
    font-size: 34px;
    line-height: 1.15;
  }
  .divider {
    position: absolute;
    left: 307px;
    top: 86px;
    width: 2px;
    height: 187px;
    background: var(--teal);
  }
  .identity { position: absolute; left: 337px; top: 82px; }
  .identity__name {
    color: var(--purple);
    font-weight: 900;
    font-size: 37px;
    letter-spacing: -0.3px;
    line-height: 1;
    text-transform: uppercase;
  }
  .identity__role {
    color: var(--pink);
    font-size: 21px;
    margin-top: 4px;
    letter-spacing: 0.4px;
  }
  .contacts { position: absolute; left: 345px; top: 172px; list-style: none; }
  .contacts li {
    display: flex;
    align-items: center;
    height: 28.5px;
    color: var(--ink);
    font-size: 19.5px;
    letter-spacing: 0.2px;
  }
  .contacts li:first-child { font-size: 22px; }
  .contacts svg { width: 20px; height: 20px; margin-right: 11px; flex: none; fill: var(--pink); }

  .footer-band {
    position: absolute;
    left: 0;
    right: 0;
    bottom: 0;
    height: 78px;
    background: linear-gradient(90deg, var(--purple) 0%, var(--purple) 60%, var(--teal) 100%);
  }

  .back-brand {
    position: absolute;
    inset: 0;
    display: flex;
    flex-direction: column;
    align-items: center;
    justify-content: center;
    color: var(--purple);
    font-weight: 400;
    line-height: 1;
  }
  .back-brand__main { font-size: 76px; letter-spacing: 0.5px; }
  .back-brand__sub { font-size: 42px; margin-top: 6px; letter-spacing: 0.5px; }
</style>
</head>
<body>
  <section class="card card--front">
    <div class="front-brand">Harborlight<br>Elder Aides</div>
    <div class="divider"></div>
    <div class="identity">
      <h1 class="identity__name">Delia Parkhurst</h1>
      <p class="identity__role">Owner</p>
    </div>
    <ul class="contacts">
      <li>
        <svg viewBox="0 0 24 24"><path d="M6.6 10.8a15.2 15.2 0 0 0 6.6 6.6l2.2-2.2a1 1 0 0 1 1-.25 11.4 11.4 0 0 0 3.6.57 1 1 0 0 1 1 1V20a1 1 0 0 1-1 1A17 17 0 0 1 3 4a1 1 0 0 1 1-1h3.5a1 1 0 0 1 1 1c0 1.25.2 2.45.57 3.57a1 1 0 0 1-.25 1z"/></svg>
        936.482.5079
      </li>
      <li>
        <svg viewBox="0 0 24 24"><path d="M3 5h18v14H3V5zm2 2v.4l7 5 7-5V7H5zm0 2.9V17h14V9.9l-7 5-7-5z"/></svg>
        Delia@harborlightelderaides.com
      </li>
      <li>
        <svg viewBox="0 0 24 24"><path d="M12 2a10 10 0 1 0 0 20 10 10 0 0 0 0-20zm-1 17.9A8 8 0 0 1 4.2 10.3L9 15v1a2 2 0 0 0 2 2zm6.9-2.5A2 2 0 0 0 16 16h-1v-3a1 1 0 0 0-1-1H8v-2h2a1 1 0 0 0 1-1V7h2a2 2 0 0 0 2-2v-.4a8 8 0 0 1 2.9 12.8z"/></svg>
        www.HarborlightElderAides.com
      </li>
      <li>
        <svg viewBox="0 0 24 24"><path d="M12 2a7 7 0 0 0-7 7c0 5.2 7 13 7 13s7-7.8 7-13a7 7 0 0 0-7-7zm0 9.5A2.5 2.5 0 1 1 12 6.5a2.5 2.5 0 0 1 0 5z"/></svg>
        Brindle Falls, Texas
      </li>
    </ul>
    <div class="footer-band" role="img" aria-label="Decorative purple and teal band along the bottom edge"></div>
  </section>

  <section class="card card--back">
    <div class="back-brand">
      <span class="back-brand__main">Harborlight</span>
      <span class="back-brand__sub">Elder Aides</span>
    </div>
  </section>
</body>
</html>
```